A design led business card for the construction industry

High-end business card to match logo. White logo on dark grey/off black to the front. Matching dark font on white to back, possibly with logo design again.

We offer construction and project management services to commercial and private clients in the UK. Projetcs range from newbuilds, conversion of listed buildings and refurbishments and extensions of existing homes. Our focus is on quality and attention to detail using the highest skills.

Contact Information for Business Card

Name; Dorian Keble BSc
Position; Project Manager
Mobile; 07962 408 175
Tel; 01632 960457
email; dorian@stonevale.co.uk
web; www.stonevale.co.uk
Address; Ashcombe on Wey, KX4 7PW

Colors

Designer to choose only greyscale colors for use in the design.

Requirements
Must have
• To include the below description of the business,

CONSTRUCTION - PROJECT MANAGEMENT
Nice to have
• The posibility of the top back of the card being used as a ruler. So will have a measurement to scale in mm or an architect scale of 1:50
Should not have
• Should not be portrait

```html
<!DOCTYPE html>
<html lang="en">
<head>
<meta charset="utf-8">
<title>Stonevale – Business Card</title>
<link rel="stylesheet" href="https://fonts.googleapis.com/css2?family=Arimo:wght@400;700&display=swap">
<style>
  :root {
    --page: #d9d9d9;
    --card-dark: #2a2a2a;
    --card-light: #ffffff;
    --ink-dark: #111111;
    --ink-light: #e6e6e6;
    --ink-muted: #a8a8a8;
    --rule: #6e6e6e;
  }
  * { margin: 0; padding: 0; box-sizing: border-box; }
  html, body {
    width: 1200px; height: 1040px; overflow: hidden;
    background: var(--page);
    font-family: "Arimo", Arial, sans-serif;
  }
  .card {
    position: absolute;
    left: 240px;
    width: 720px; height: 420px;
    box-shadow: 0 10px 30px rgba(0,0,0,0.25);
  }
  .card--front {
    top: 70px;
    background: var(--card-dark);
    border-radius: 70px 0 70px 0;
    display: flex; flex-direction: column; align-items: center; justify-content: center;
    color: var(--ink-light);
  }
  .card--back {
    top: 550px;
    background: var(--card-light);
    border-radius: 0 70px 0 70px;
    color: var(--ink-dark);
    display: flex; align-items: center;
  }
  .brand {
    display: flex; align-items: center; gap: 18px;
  }
  .brand__square {
    width: 26px; height: 26px; background: currentColor; flex: none;
  }
  .brand__name {
    font-size: 34px; font-weight: 400;
    letter-spacing: 0.42em;
    text-transform: uppercase;
    white-space: nowrap;
  }
  .tagline {
    margin-top: 30px;
    font-size: 17px; letter-spacing: 0.04em;
    color: var(--ink-muted);
  }
  .back__brand {
    width: 360px;
    display: flex; justify-content: center;
  }
  .back__brand .brand { gap: 14px; }
  .back__brand .brand__square { width: 22px; height: 22px; }
  .back__brand .brand__name { font-size: 27px; letter-spacing: 0.36em; }
  .back__rule {
    width: 1px; height: 240px; background: var(--rule); flex: none;
  }
  .contact {
    padding-left: 36px;
  }
  .contact__name { font-size: 25px; font-weight: 700; }
  .contact__name span { font-weight: 400; }
  .contact__role { font-size: 21px; margin-top: 2px; }
  .contact__list { list-style: none; margin-top: 22px; }
  .contact__list li {
    display: flex; align-items: center; gap: 10px;
    font-size: 22px; line-height: 30px;
  }
  .contact__list svg { width: 20px; height: 20px; flex: none; }
  .contact__address { font-size: 22px; margin-top: 18px; }
</style>
</head>
<body>
  <section class="card card--front">
    <div class="brand">
      <span class="brand__square"></span>
      <span class="brand__name">Stonevale</span>
    </div>
    <p class="tagline">CONSTRUCTION - PROJECT MANAGEMENT</p>
  </section>

  <section class="card card--back">
    <div class="back__brand">
      <div class="brand">
        <span class="brand__square"></span>
        <span class="brand__name">Stonevale</span>
      </div>
    </div>
    <div class="back__rule"></div>
    <div class="contact">
      <p class="contact__name">DORIAN KEBLE <span>BSc</span></p>
      <p class="contact__role">Project Manager</p>
      <ul class="contact__list">
        <li>
          <svg viewBox="0 0 20 20" aria-hidden="true"><rect x="5" y="1.5" width="10" height="17" rx="2" fill="none" stroke="currentColor" stroke-width="1.8"/><line x1="8.5" y1="15.5" x2="11.5" y2="15.5" stroke="currentColor" stroke-width="1.6"/></svg>
          07962 408 175
        </li>
        <li>
          <svg viewBox="0 0 20 20" aria-hidden="true"><path d="M5 2.5l3 3-1.8 2.2a11 11 0 0 0 6.1 6.1L14.5 12l3 3-2.2 2.5C9 17 3 11 2.5 4.7z" fill="currentColor"/></svg>
          01632 960457
        </li>
        <li>
          <svg viewBox="0 0 20 20" aria-hidden="true"><rect x="1.5" y="4" width="17" height="12" fill="currentColor"/><polyline points="1.5,4 10,11 18.5,4" fill="none" stroke="#fff" stroke-width="1.4"/></svg>
          dorian@stonevale.co.uk
        </li>
        <li>
          <svg viewBox="0 0 20 20" aria-hidden="true" fill="none" stroke="currentColor" stroke-width="1.5"><circle cx="10" cy="10" r="8"/><ellipse cx="10" cy="10" rx="3.5" ry="8"/><line x1="2" y1="10" x2="18" y2="10"/><line x1="3.5" y1="6" x2="16.5" y2="6"/><line x1="3.5" y1="14" x2="16.5" y2="14"/></svg>
          www.stonevale.co.uk
        </li>
      </ul>
      <p class="contact__address">Ashcombe on Wey, KX4 7PW</p>
    </div>
  </section>
</body>
</html>
```